Ridgeline Journeys business card

please see website
www.ridgelinejourneys.comau

info needed on card
Curtis Halvey
Ph
email
Adventure Riding GPS trails

please use my logo and colours off my site

Curtis Halvey
curtis@ridgelinejourneys.com

```html
<!DOCTYPE html>
<html lang="en">
<head>
<meta charset="utf-8">
<title>Ridgeline Journeys – Business Card</title>
<link rel="stylesheet" href="https://fonts.googleapis.com/css2?family=Oswald:wght@700&family=Roboto:wght@400;700&display=swap">
<style>
  :root {
    --ink: #0b0b0b;
    --paper: #ffffff;
    --brand-yellow: #f5d60c;
    --muted: #8a8a8a;
    --text-grey: #555555;
    --stage: #2a2a2a;
  }
  * { box-sizing: border-box; margin: 0; padding: 0; }
  html, body {
    width: 1200px; height: 750px; overflow: hidden;
    background: var(--stage);
    font-family: "Roboto", Arial, sans-serif;
  }
  .canvas {
    width: 1200px; height: 750px;
    display: flex; align-items: center; justify-content: center; gap: 60px;
  }
  .card {
    position: relative;
    width: 510px; height: 292px;
    overflow: hidden;
    box-shadow: 0 12px 30px rgba(0,0,0,.45);
  }
  .card--front { background: var(--ink); }
  .card--back { background: var(--paper); }

  .brand {
    display: flex; align-items: center; gap: 14px;
  }
  .brand__dot {
    width: 34px; height: 34px; border-radius: 50%;
    background: var(--brand-yellow);
    flex: none;
  }
  .brand__name {
    font-family: "Oswald", Impact, sans-serif;
    font-weight: 700;
    text-transform: uppercase;
    line-height: 1;
    font-size: 34px;
    letter-spacing: .5px;
  }
  .card--front .brand__name { color: var(--paper); }
  .card--back .brand__name { color: var(--ink); }

  .tagline {
    font-size: 13px;
    letter-spacing: .3px;
  }

  .card--front .front-stack {
    position: absolute; inset: 0;
    display: flex; flex-direction: column; align-items: center; justify-content: center; gap: 30px;
  }
  .card--front .tagline { color: var(--paper); }

  .back-brand {
    position: absolute; left: 92px; top: 44px;
    display: flex; flex-direction: column; gap: 12px;
  }
  .back-brand .tagline { color: var(--text-grey); padding-left: 48px; }

  .name-band {
    position: absolute; left: 0; top: 0; width: 510px; height: 292px;
  }
  .holder-name {
    position: absolute; left: 150px; top: 168px;
    color: var(--brand-yellow);
    font-weight: 700; font-size: 19px;
  }

  .contacts {
    position: absolute; left: 150px; top: 226px;
    display: flex; flex-direction: column; gap: 7px;
    color: var(--text-grey); font-size: 11.5px;
  }
  .contacts__row { display: flex; align-items: center; gap: 16px; }
  .contact { display: flex; align-items: center; gap: 6px; }
  .contact svg { width: 13px; height: 13px; flex: none; }
</style>
</head>
<body>
<main class="canvas">

  <section class="card card--front" aria-label="Card front">
    <div class="front-stack">
      <div class="brand">
        <span class="brand__dot"></span>
        <span class="brand__name">Ridgeline<br>Journeys</span>
      </div>
      <p class="tagline">Adventure Riding GPS trails</p>
    </div>
  </section>

  <section class="card card--back" aria-label="Card back">
    <div class="back-brand">
      <div class="brand">
        <span class="brand__dot"></span>
        <span class="brand__name">Ridgeline<br>Journeys</span>
      </div>
      <p class="tagline">Adventure Riding GPS trails</p>
    </div>

    <svg class="name-band" viewBox="0 0 510 292" aria-hidden="true">
      <polygon points="0,158 330,158 380,118 510,118 510,158 510,208 0,208" fill="#0b0b0b"/>
    </svg>
    <p class="holder-name">Curtis Halvey</p>

    <div class="contacts">
      <div class="contacts__row">
        <span class="contact">
          <svg viewBox="0 0 16 16" aria-hidden="true"><path fill="#f5d60c" d="M3.6 1.5l2.3 2.6-1.3 1.8c.9 1.9 2.4 3.4 4.3 4.3l1.8-1.3 2.6 2.3-1.4 2.3C6.6 13.3 2.7 9.4 1.3 3z"/></svg>
          555 0142 7789
        </span>
        <span class="contact">
          <svg viewBox="0 0 16 16" aria-hidden="true"><rect x="1" y="3" width="14" height="10" rx="1" fill="#f5d60c"/><path d="M1.5 3.8L8 9l6.5-5.2" fill="none" stroke="#fff" stroke-width="1.3"/></svg>
          curtis@ridgelinejourneys.com
        </span>
      </div>
      <div class="contacts__row">
        <span class="contact">
          <svg viewBox="0 0 16 16" aria-hidden="true"><circle cx="8" cy="8" r="7" fill="#f5d60c"/><path d="M1 8h14M8 1c-3 3.5-3 10.5 0 14M8 1c3 3.5 3 10.5 0 14" fill="none" stroke="#fff" stroke-width="1"/></svg>
          www.ridgelinejourneys.comau
        </span>
      </div>
    </div>
  </section>

</main>
</body>
</html>
```